Design a New Business Card for Our Company

We are looking for fresh, unique, and a modern business card that reflects our roots as digital marketing agency focused on SEM.

Industry/Entity Type

Marketing

Contact Information for Business Card

looking for very unique out of the box designs. clean and modern that compliments our logo

Requirements
Must have
• colors should match our logo
• Front should have name, address, email, and phone/fax of the person, phone/fax are the same number
• back should have our url

```html
<!DOCTYPE html>
<html lang="en">
<head>
<meta charset="utf-8">
<title>Brightlane Business Card</title>
<link href="https://fonts.googleapis.com/css2?family=Open+Sans:wght@400;600&display=swap" rel="stylesheet">
<style>
  :root {
    --page-bg: #3c3c3c;
    --card-white: #ffffff;
    --card-grey: #b3b3b3;
    --brand-blue: #5b97d0;
    --brand-grey: #9b9b9b;
    --text-dark: #4a4a4a;
    --icon-grey: #8c8c8c;
    --white: #ffffff;
  }
  * { margin: 0; padding: 0; box-sizing: border-box; }
  html, body {
    width: 1105px;
    height: 1200px;
    overflow: hidden;
    background: var(--page-bg);
    font-family: "Open Sans", Arial, sans-serif;
  }
  .stage {
    position: relative;
    width: 1105px;
    height: 1200px;
  }
  .card {
    position: absolute;
    left: 192px;
    width: 722px;
    height: 412px;
  }
  .card-front { top: 166px; background: var(--card-white); }
  .card-back  { top: 622px; background: var(--card-grey); }

  /* Front */
  .name-band {
    position: absolute;
    left: 0;
    top: 55px;
    width: 371px;
    height: 78px;
    background: var(--brand-blue);
    color: var(--white);
    padding: 8px 0 0 46px;
  }
  .person-name { font-size: 25px; font-weight: 600; line-height: 1.3; }
  .person-title { font-size: 19px; font-weight: 400; line-height: 1.2; }

  .brand {
    position: absolute;
    display: flex;
    align-items: center;
    gap: 12px;
  }
  .brand-front { left: 376px; top: 66px; }
  .brand-mark { width: 40px; height: 40px; border-radius: 50%; background: var(--brand-blue); flex: none; }
  .brand-name {
    font-size: 46px;
    font-weight: 600;
    line-height: 1;
    letter-spacing: -1px;
    color: var(--brand-grey);
  }

  .contact-list {
    position: absolute;
    left: 46px;
    top: 290px;
    list-style: none;
    font-size: 19px;
    color: var(--text-dark);
  }
  .contact-list li {
    display: flex;
    align-items: center;
    gap: 9px;
    height: 27.5px;
  }
  .contact-list svg { width: 18px; height: 18px; fill: var(--icon-grey); flex: none; }

  .address {
    position: absolute;
    right: 47px;
    top: 318px;
    font-style: normal;
    text-align: right;
    font-size: 19px;
    line-height: 27.5px;
    color: var(--text-dark);
  }

  /* Back */
  .brand-back {
    left: 0;
    right: 0;
    top: 172px;
    justify-content: center;
  }
  .brand-back .brand-mark { width: 56px; height: 56px; background: var(--white); }
  .brand-back .brand-name { font-size: 64px; color: var(--white); }

  .website {
    position: absolute;
    left: 0;
    right: 0;
    top: 348px;
    text-align: center;
    font-size: 18px;
    letter-spacing: 4px;
    color: var(--white);
  }
</style>
</head>
<body>
<main class="stage">
  <section class="card card-front" aria-label="Business card front">
    <div class="name-band">
      <p class="person-name">Mara Ellison</p>
      <p class="person-title">CEO/Founder</p>
    </div>

    <div class="brand brand-front">
      <span class="brand-mark"></span>
      <span class="brand-name">Brightlane</span>
    </div>

    <ul class="contact-list">
      <li>
        <svg viewBox="0 0 24 24" aria-hidden="true"><path d="M6.6 10.8a15.1 15.1 0 0 0 6.6 6.6l2.2-2.2a1 1 0 0 1 1-.25 11.4 11.4 0 0 0 3.6.57 1 1 0 0 1 1 1V20a1 1 0 0 1-1 1A17 17 0 0 1 3 4a1 1 0 0 1 1-1h3.5a1 1 0 0 1 1 1c0 1.25.2 2.45.57 3.57a1 1 0 0 1-.25 1z"/></svg>
        <span>555 210 4817</span>
      </li>
      <li>
        <svg viewBox="0 0 24 24" aria-hidden="true"><path d="M6 3h12v5H6z M3 9h18a1 1 0 0 1 1 1v8h-4v3H6v-3H2v-8a1 1 0 0 1 1-1z M8 15v4h8v-4z"/></svg>
        <span>555 210 4818</span>
      </li>
      <li>
        <svg viewBox="0 0 24 24" aria-hidden="true"><path d="M2 5h20v14H2z M3.5 6.5 12 13l8.5-6.5z" fill-rule="evenodd"/></svg>
        <span>mara@brightlane.com</span>
      </li>
    </ul>

    <address class="address">
      1420 Cedar Hollow Road<br>
      Fairview, Oregon 97024
    </address>
  </section>

  <section class="card card-back" aria-label="Business card back">
    <div class="brand brand-back">
      <span class="brand-mark"></span>
      <span class="brand-name">Brightlane</span>
    </div>
    <p class="website">www.brightlane.com</p>
  </section>
</main>
</body>
</html>
```